Business Card Design

I already have a company logo for my company. I have a logo for the manufacturer we represent. I want a professional business card design.

```html
<!DOCTYPE html>
<html lang="en">
<head>
<meta charset="utf-8">
<title>Caution Works LLC — Business Card</title>
<link rel="stylesheet" href="https://fonts.googleapis.com/css2?family=Saira:wght@400;600;700&display=swap">
<style>
  :root {
    --page: #2a2a2a;
    --card-black: #161616;
    --card-back: #1b1b1b;
    --red: #e3262b;
    --silver-light: #e2e2e2;
    --silver-mid: #bdbdbd;
    --silver-dark: #9a9a9a;
    --ink: #1d1d1d;
    --ink-soft: #2e2e2e;
    --white: #f2f2f2;
  }
  html, body {
    margin: 0;
    padding: 0;
    width: 1200px;
    height: 1200px;
    overflow: hidden;
    background: var(--page);
    font-family: "Saira", sans-serif;
  }
  .canvas {
    position: relative;
    width: 1200px;
    height: 1200px;
  }
  .card {
    position: absolute;
    left: 200px;
    width: 798px;
    height: 455px;
    overflow: hidden;
  }
  .card-front { top: 96px; background: var(--card-black); }
  .card-back { top: 654px; background: var(--card-back); }

  .front-panels {
    position: absolute;
    inset: 0;
    width: 100%;
    height: 100%;
  }

  .brand {
    position: absolute;
    display: flex;
    align-items: center;
    gap: 12px;
    color: var(--white);
    font-weight: 700;
    letter-spacing: 1px;
    white-space: nowrap;
  }
  .brand-mark {
    background: var(--red);
    flex: none;
  }
  .brand-front {
    left: 190px;
    top: 156px;
    transform: translate(-50%, -50%);
    font-size: 27px;
  }
  .brand-front .brand-mark { width: 22px; height: 22px; }
  .brand-back {
    left: 399px;
    top: 228px;
    transform: translate(-50%, -50%);
    font-size: 42px;
    gap: 18px;
  }
  .brand-back .brand-mark { width: 34px; height: 34px; }

  .contact {
    position: absolute;
    right: 48px;
    top: 0;
    text-align: right;
    color: var(--ink);
  }
  .contact-name {
    position: absolute;
    right: 0;
    top: 108px;
    margin: 0;
    font-size: 39px;
    font-weight: 600;
    letter-spacing: 2px;
    line-height: 1;
    white-space: nowrap;
  }
  .contact-role {
    position: absolute;
    right: 0;
    top: 154px;
    margin: 0;
    font-size: 22px;
    color: var(--ink-soft);
    letter-spacing: 1px;
    line-height: 1;
    white-space: nowrap;
  }
  .contact-address {
    position: absolute;
    right: 0;
    top: 207px;
    margin: 0;
    font-size: 21px;
    line-height: 29px;
    font-style: normal;
    letter-spacing: 0.5px;
    white-space: nowrap;
  }
  .contact-lines {
    position: absolute;
    right: 0;
    top: 273px;
    margin: 0;
    padding: 0;
    list-style: none;
  }
  .contact-lines li {
    display: flex;
    justify-content: flex-end;
    align-items: center;
    gap: 12px;
    height: 29px;
    font-size: 21px;
    letter-spacing: 0.5px;
    white-space: nowrap;
  }
  .contact-icon {
    width: 18px;
    height: 18px;
    flex: none;
    fill: var(--ink);
  }
</style>
</head>
<body>
<main class="canvas">

  <section class="card card-front" aria-label="Business card front">
    <svg class="front-panels" viewBox="0 0 798 455" preserveAspectRatio="none" aria-hidden="true">
      <defs>
        <linearGradient id="silver" x1="0" y1="0" x2="1" y2="0.3">
          <stop offset="0" stop-color="#a8a8a8"/>
          <stop offset="0.25" stop-color="#dedede"/>
          <stop offset="0.5" stop-color="#a9a9a9"/>
          <stop offset="0.75" stop-color="#d6d6d6"/>
          <stop offset="1" stop-color="#9e9e9e"/>
        </linearGradient>
      </defs>
      <polygon points="486,0 506,0 309,455 289,455" fill="var(--red)"/>
      <polygon points="506,0 798,0 798,455 309,455" fill="url(#silver)"/>
    </svg>

    <div class="brand brand-front">
      <span class="brand-mark"></span>
      <span>CAUTION WORKS LLC</span>
    </div>

    <div class="contact">
      <h1 class="contact-name">JOHN SMITH</h1>
      <p class="contact-role">Founder &amp; CEO</p>
      <address class="contact-address">423 Street Address, City<br>State &amp; ZIP Code Country</address>
      <ul class="contact-lines">
        <li>(123) 456-7890
          <svg class="contact-icon" viewBox="0 0 24 24" aria-label="Phone"><path d="M6.6 10.8a15 15 0 0 0 6.6 6.6l2.2-2.2a1 1 0 0 1 1-.25 11.4 11.4 0 0 0 3.6.57 1 1 0 0 1 1 1V20a1 1 0 0 1-1 1A17 17 0 0 1 3 4a1 1 0 0 1 1-1h3.5a1 1 0 0 1 1 1c0 1.25.2 2.45.57 3.57a1 1 0 0 1-.25 1z"/></svg>
        </li>
        <li>(123) 456-7890
          <svg class="contact-icon" viewBox="0 0 24 24" aria-label="Mobile"><path d="M7 2h10a2 2 0 0 1 2 2v16a2 2 0 0 1-2 2H7a2 2 0 0 1-2-2V4a2 2 0 0 1 2-2zm0 3v13h10V5zm5 14.2a1 1 0 1 0 0 .01z"/></svg>
        </li>
        <li>(123) 456-7890
          <svg class="contact-icon" viewBox="0 0 24 24" aria-label="Fax"><path d="M7 3h10v4H7zM4 8h16a2 2 0 0 1 2 2v6h-4v5H6v-5H2v-6a2 2 0 0 1 2-2zm4 8v3h8v-3z"/></svg>
        </li>
        <li>info@yourwebsitehere.com
          <svg class="contact-icon" viewBox="0 0 24 24" aria-label="Email"><path d="M2 5h20v14H2zm2 2v.5l8 5 8-5V7z"/></svg>
        </li>
        <li>yourwebsitehere.com
          <svg class="contact-icon" viewBox="0 0 24 24" aria-label="Website"><path d="M12 2a10 10 0 1 0 0 20 10 10 0 0 0 0-20zm0 2a8 8 0 0 1 7.7 6H16l-2-2-3 1-1-2 2-3zM4.3 10H7l2 3-1 3 2 2v2.9A8 8 0 0 1 4.3 10zm9.7 9.8V17l3-3h2.8a8 8 0 0 1-5.8 5.8z"/></svg>
        </li>
      </ul>
    </div>
  </section>

  <section class="card card-back" aria-label="Business card back">
    <div class="brand brand-back">
      <span class="brand-mark"></span>
      <span>CAUTION WORKS LLC</span>
    </div>
  </section>

</main>
</body>
</html>
```